Renny Oskow - Free Personalised Health Consultation - "One size does not fit all"

This flyer will be left on tables/seats at speaking events and seminars and used to attain leads.

Top half will have "SMS me for a FREE Personalised Health Consultation" and my picture (see www.rennyoskow-demo.com and pick most engaging photo) and underneath my contact details. It must have lines with "Notes:" halfway down so people can take notes at the seminar and lines on the back with my contact details again and "Notes: with lines.

I am having a business card also being designed by Artvane for same and would like the flyer and business card to carry a similar feel/look for consistency.

Below is the brief for the business card being designed:
Business Card for www.rennyoskow-demo.com site. It is a trust site and I use it for 1:1 relatable connections. It is the one I use for building intimate 1:1 trust building and Exec Coaching Services and programs for high wealth individuals and corporates. I also have a commercial programmatic site of my personal health products and services and programs for main stream one to many. www.steadyforwardliving-demo.com that can also provoke thought for the www.rennyoskow-demo.com business card. (mind you will get a separate business card for that site, but want to provide context). It has a logo which you may want to draw from in designing the rennyoskow business card which is personal and is about building my brand. There is also a rennyoskow personal PX page and rennyoskow business PX page. I am a Certified Talent Compass 3.1 Coach with Norvik and you can get a corporate brief of me on there to give you more context https://www.norvikcoachhub-demo.com/coach/en-us/directory?search=renny

Target Market(s)

Exec, IT, Health conscious. Corporates wanting to run Health and Wellness programs. Those wanting to go from good to great. Millennials to Middleaged.

Industry/Entity Type

Health And Wellness

Font styles to use
Sans Serif
Other font styles liked:
• Arial and Calibri ok too

Colors

Designer to choose colors to be used in the design.

Requirements
Must have
• Picture of me - use best from www.rennyoskow-demo.com or can send one you choose.
• Contact details like my buisness card being designed by you guys in separate project.
• Name: Renny Oskow
• email: renny@rennyoskow-demo.,com
• Phone: Australia +61 400 000 137 Singapore: +65 9000 2468
Nice to have
• Open to ideas

```html
<!DOCTYPE html>
<html lang="en">
<head>
<meta charset="utf-8">
<title>Renny Oskow – Health Consultation Notes Flyer</title>
<link rel="stylesheet" href="https://fonts.googleapis.com/css2?family=Roboto:wght@400;900&family=Caveat:wght@400&display=swap">
<style>
  :root {
    --backdrop: #000000;
    --paper: #ffffff;
    --brand-blue: #00ace6;
    --soft-blue: #cfeaf7;
    --mist-grey: #eeeeee;
    --rule-grey: #cfcfcf;
    --ink: #111111;
    --photo-dark: #3a3a3a;
    --photo-light: #d9d9d9;
  }
  * { box-sizing: border-box; margin: 0; padding: 0; }
  html, body {
    width: 1200px; height: 835px; overflow: hidden;
    background: var(--backdrop);
    font-family: "Roboto", Arial, sans-serif;
  }
  .sheet {
    position: absolute; top: 77px;
    width: 483px; height: 682px;
    background: var(--paper);
    overflow: hidden;
  }
  .sheet--front { left: 88px; }
  .sheet--back { left: 629px; }
  .sheet__art { position: absolute; inset: 0; }

  .signature {
    position: absolute;
    font-family: "Caveat", "Segoe Script", "Bradley Hand", "Brush Script MT", cursive;
    font-style: italic;
    color: var(--ink);
    white-space: nowrap;
    line-height: 1;
  }
  .signature--front { left: 176px; top: 120px; font-size: 32px; }
  .signature--ghost {
    left: 262px; top: 160px; font-size: 74px;
    color: #000; opacity: .05;
  }
  .signature--back {
    right: 12px; top: 624px; font-size: 22px;
    width: 108px; overflow: hidden; text-align: right;
  }

  .offer {
    position: absolute; left: 103px; top: 262px;
    color: var(--paper); font-weight: 900;
    text-transform: uppercase; letter-spacing: .4px;
  }
  .offer__line { display: block; white-space: nowrap; }
  .offer__line--lead { font-size: 35px; line-height: 40px; }
  .offer__small { font-size: 23px; }
  .offer__line--rest { font-size: 26px; line-height: 37px; }
  .offer__free {
    display: inline-block; background: var(--paper); color: var(--ink);
    padding: 0 7px; line-height: 26px;
  }

  .contact {
    position: absolute; color: var(--paper);
    font-size: 8.6px; letter-spacing: .1px; text-transform: uppercase;
    white-space: nowrap;
  }
  .contact__row { position: absolute; display: flex; align-items: center; height: 12px; }
  .contact__icon { position: absolute; width: 8px; height: 8px; }
  .contact__divider { position: absolute; width: 1px; height: 34px; background: #888; }
</style>
</head>
<body>

<section class="sheet sheet--front">
  <svg class="sheet__art" width="483" height="682" viewBox="0 0 483 682">
    <defs>
      <linearGradient id="photoFadeFront" x1="0" y1="0" x2="0" y2="1">
        <stop offset="0" stop-color="var(--photo-light)"/>
        <stop offset=".35" stop-color="var(--photo-dark)"/>
        <stop offset=".85" stop-color="#777"/>
        <stop offset="1" stop-color="#ffffff" stop-opacity="0"/>
      </linearGradient>
    </defs>
    <circle cx="268" cy="142" r="134" fill="var(--mist-grey)"/>
    <circle cx="349" cy="26" r="13" fill="var(--soft-blue)"/>
    <circle cx="358" cy="44" r="5" fill="var(--soft-blue)"/>
    <circle cx="66" cy="172" r="73" fill="var(--brand-blue)"/>
    <path role="img" aria-label="Portrait photo of Renny Oskow smiling, arms crossed, black t-shirt"
          d="M60 14 Q92 0 118 14 L130 95 Q150 110 200 130 Q240 160 262 240 L262 440 L0 440 L0 200 Q30 150 68 125 L60 95 Z"
          fill="url(#photoFadeFront)"/>
    <rect x="82" y="239" width="375" height="182" fill="var(--brand-blue)"/>
    <polygon points="102,394 448,394 437,439 102,439" fill="var(--ink)"/>
    <g stroke="var(--rule-grey)" stroke-width="1">
      <line x1="19" y1="475" x2="464" y2="475"/><line x1="19" y1="502" x2="464" y2="502"/>
      <line x1="19" y1="529" x2="464" y2="529"/><line x1="19" y1="556" x2="464" y2="556"/>
      <line x1="19" y1="583" x2="464" y2="583"/><line x1="19" y1="610" x2="464" y2="610"/>
      <line x1="19" y1="637" x2="464" y2="637"/><line x1="19" y1="664" x2="464" y2="664"/>
    </g>
  </svg>

  <span class="signature signature--ghost">Oskow</span>
  <span class="signature signature--front">Renny Oskow</span>

  <h1 class="offer">
    <span class="offer__line offer__line--lead">SMS me <span class="offer__small">for</span></span>
    <span class="offer__line offer__line--rest">A <span class="offer__free">Free</span> Personalised</span>
    <span class="offer__line offer__line--rest">Health Consultation</span>
  </h1>

  <div class="contact">
    <svg class="contact__icon" style="left:118px;top:404px" viewBox="0 0 10 10"><path d="M2 0.5 L4 2.8 L3 4 Q4 6 6 7 L7.2 6 L9.5 8 L8 9.6 Q1 8 0.4 2 Z" fill="#fff"/></svg>
    <div class="contact__row" style="left:130px;top:402px">Australia:&nbsp; +61 400 000 137</div>
    <div class="contact__row" style="left:130px;top:418px">Singapore: +65 9000 2468</div>
    <span class="contact__divider" style="left:262px;top:399px"></span>
    <svg class="contact__icon" style="left:273px;top:404px" viewBox="0 0 10 10"><rect x="0.5" y="2" width="9" height="6.5" fill="#fff"/><path d="M0.5 2 L5 5.6 L9.5 2" stroke="#111" stroke-width="1" fill="none"/></svg>
    <div class="contact__row" style="left:285px;top:402px">renny@rennyoskow-demo.com</div>
    <svg class="contact__icon" style="left:273px;top:420px" viewBox="0 0 10 10"><circle cx="5" cy="5" r="4.5" fill="#fff"/><path d="M2 3 Q4 4 3.5 6 M6 1.5 Q7 4 8.5 5" stroke="#111" stroke-width="1.2" fill="none"/></svg>
    <div class="contact__row" style="left:285px;top:418px">www.rennyoskow-demo.com</div>
  </div>
</section>

<section class="sheet sheet--back">
  <svg class="sheet__art" width="483" height="682" viewBox="0 0 483 682">
    <defs>
      <linearGradient id="photoFadeBack" x1="0" y1="0" x2="0" y2="1">
        <stop offset="0" stop-color="#bdbdbd"/>
        <stop offset=".55" stop-color="#4a4a4a"/>
        <stop offset="1" stop-color="#8a8a8a"/>
      </linearGradient>
    </defs>
    <circle cx="415" cy="710" r="70" fill="var(--mist-grey)"/>
    <g stroke="var(--rule-grey)" stroke-width="1">
      <line x1="19" y1="32" x2="464" y2="32"/><line x1="19" y1="59" x2="464" y2="59"/>
      <line x1="19" y1="86" x2="464" y2="86"/><line x1="19" y1="113" x2="464" y2="113"/>
      <line x1="19" y1="140" x2="464" y2="140"/><line x1="19" y1="167" x2="464" y2="167"/>
      <line x1="19" y1="194" x2="464" y2="194"/><line x1="19" y1="221" x2="464" y2="221"/>
      <line x1="19" y1="248" x2="464" y2="248"/><line x1="19" y1="275" x2="464" y2="275"/>
      <line x1="19" y1="302" x2="464" y2="302"/><line x1="19" y1="329" x2="464" y2="329"/>
      <line x1="19" y1="356" x2="464" y2="356"/><line x1="19" y1="383" x2="464" y2="383"/>
      <line x1="19" y1="410" x2="464" y2="410"/><line x1="19" y1="437" x2="464" y2="437"/>
      <line x1="19" y1="464" x2="464" y2="464"/>
      <line x1="83" y1="491" x2="464" y2="491"/><line x1="108" y1="518" x2="464" y2="518"/>
      <line x1="128" y1="545" x2="464" y2="545"/><line x1="136" y1="572" x2="464" y2="572"/>
    </g>
    <path role="img" aria-label="Small portrait photo of Renny Oskow, black t-shirt"
          d="M34 480 Q50 464 68 480 L72 530 Q110 545 128 580 L124 620 L0 620 L0 556 Q20 538 36 532 Z"
          fill="url(#photoFadeBack)"/>
    <rect x="0" y="652" width="483" height="30" fill="var(--brand-blue)"/>
    <polygon points="0,618 356,618 345,665 0,665" fill="var(--ink)"/>
    <line x1="368" y1="648" x2="472" y2="648" stroke="#555" stroke-width="0.8"/>
  </svg>

  <span class="signature signature--back">Renny Oskow</span>

  <div class="contact">
    <svg class="contact__icon" style="left:17px;top:629px" viewBox="0 0 10 10"><path d="M2 0.5 L4 2.8 L3 4 Q4 6 6 7 L7.2 6 L9.5 8 L8 9.6 Q1 8 0.4 2 Z" fill="#fff"/></svg>
    <div class="contact__row" style="left:29px;top:627px">Australia:&nbsp; +61 400 000 137</div>
    <div class="contact__row" style="left:29px;top:643px">Singapore: +65 9000 2468</div>
    <span class="contact__divider" style="left:164px;top:624px"></span>
    <svg class="contact__icon" style="left:174px;top:629px" viewBox="0 0 10 10"><rect x="0.5" y="2" width="9" height="6.5" fill="#fff"/><path d="M0.5 2 L5 5.6 L9.5 2" stroke="#111" stroke-width="1" fill="none"/></svg>
    <div class="contact__row" style="left:186px;top:627px">renny@rennyoskow-demo.com</div>
    <svg class="contact__icon" style="left:174px;top:645px" viewBox="0 0 10 10"><circle cx="5" cy="5" r="4.5" fill="#fff"/><path d="M2 3 Q4 4 3.5 6 M6 1.5 Q7 4 8.5 5" stroke="#111" stroke-width="1.2" fill="none"/></svg>
    <div class="contact__row" style="left:186px;top:643px">www.rennyoskow-demo.com</div>
  </div>
</section>

</body>
</html>
```